Reach Crafters Unique Marketing Website Design

I am starting a new company that is a thought leader in the marketing consulting space. The company is called Reach Crafters. We intend to build a Wordpress site on the Astra Theme with the Spectra builder. Our goal is to become the leading voice that empowers high-ticket service business leaders to become Reach Crafters by equipping them with the cutting-edge frameworks and decision grade intelligence taught in leading business schools. What we are looking for is a website design that is clean and professional, making some use of white space well also being eye catching and distinctive in the consulting space. We will probably want to have a video on the homepage not in the hero section, but just below to explain the company and what we do. Our tagline is "Be found. Be chosen." I have attached a brand guide with some messaging, our typography choices, and our color system. The full site will have a primary nav that is four pages - About us, Services, Insights (essentially a blog), and Contact Us. The goal of this project is to develop an art direction that I can give to a designer to build loads of new pages.

Target Market(s)

Business owners (mostly male) from 30-60 years old, looking to fix their sales and marketing funnel.

Industry/Entity Type

Marketing consulting

Font styles to use
Sans Serif

Requirements
Must have
• A clean, professional design that builds trust with owners of high-ticket service businesses. We need a space for explainer video, and sections that tell prospects what we do. Would also like to have a blog carousel.
Nice to have
• Social feeds, if possible. See attached documents for colors and fonts.
Should not have
• Our feel is professional enough to be trustworthy, but unique enough to be memorable. Cartoon ideas do not meet the professional test, and we do not want the website to appear feminine.

```html
<!DOCTYPE html>
<html lang="en">
<head>
<meta charset="utf-8">
<title>Reach Crafters — Be Found. Be Chosen.</title>
<link rel="stylesheet" href="https://fonts.googleapis.com/css2?family=Oswald:wght@500;600;700&family=Inter:wght@400;500;600;700&display=swap">
<style>
:root{
  --navy:#0e1830;
  --navy-deep:#0a1226;
  --navy-mid:#1c2a4a;
  --blue:#2d4ff2;
  --purple:#7a5cf5;
  --green:#1db57c;
  --ink:#161c2c;
  --muted:#6b7285;
  --light:#f3f5fa;
  --white:#ffffff;
  --head:'Oswald',sans-serif;
  --body:'Inter',sans-serif;
}
*{margin:0;padding:0;box-sizing:border-box}
html,body{width:1200px;height:3944px;overflow:hidden}
body{position:relative;background:var(--white);font-family:var(--body);color:var(--ink)}
.abs{position:absolute}
.btn{position:absolute;display:flex;align-items:center;justify-content:center;font-family:var(--body);font-weight:700;font-size:14px;letter-spacing:.5px;text-transform:uppercase;color:var(--white);background:var(--blue);height:44px}
.btn.ghost{background:transparent;border:2px solid var(--white)}
.title{position:absolute;left:0;width:1200px;text-align:center;font-family:var(--head);font-weight:600;font-size:38px;line-height:48px;letter-spacing:1px;text-transform:uppercase;color:var(--ink)}
.title.light{color:var(--white)}
.rule{position:absolute;height:3px;width:60px;background:var(--purple)}
.photo{position:absolute}

/* hero */
.hero{position:absolute;left:0;top:0;width:1200px;height:600px;background:linear-gradient(180deg,#2a3855 0%,#1b2742 45%,#0f192f 100%)}
.hero .shade{position:absolute;inset:0;background:radial-gradient(ellipse at 50% 35%,rgba(90,110,150,.35),rgba(10,18,38,.55) 70%)}
.brand{position:absolute;font-family:var(--body);font-weight:700;color:var(--white);letter-spacing:1px}
.nav{position:absolute;top:22px;left:456px;display:flex;gap:36px;font-size:15px;font-weight:500;color:var(--white)}
.nav .active{color:var(--green)}
.hero h1{position:absolute;top:180px;left:0;width:1200px;text-align:center;font-family:var(--head);font-weight:700;font-size:70px;line-height:84px;letter-spacing:1px;color:var(--white)}
.hero .lead{position:absolute;top:286px;left:0;width:1200px;text-align:center;font-size:20px;font-weight:500;color:var(--white)}

/* about */
.about-text p{font-size:14px;line-height:24px;color:var(--muted)}

/* services */
.svc{position:absolute;top:1228px;height:280px;display:flex;align-items:center;justify-content:center;color:var(--white);font-weight:600;font-size:15px}

/* purpose band */
.purpose-band{position:absolute;left:0;top:1664px;width:1200px;height:416px;background:linear-gradient(160deg,var(--navy-mid),var(--navy) 60%,var(--navy-deep))}
.purpose-text{position:absolute;top:1810px;left:240px;width:720px;text-align:center;color:#dfe4f0;font-size:15px;line-height:24px}

/* blog */
.blog{position:absolute;left:0;top:3100px;width:1200px;height:510px;background:var(--light)}
.card{position:absolute;top:3260px;width:296px;height:320px;background:var(--white);box-shadow:0 6px 18px rgba(20,30,60,.08)}
.card .img{height:200px}
.card .date{position:absolute;left:18px;top:216px;font-size:13px;color:var(--purple);display:flex;align-items:center;gap:8px}
.card h3{position:absolute;left:18px;top:244px;width:260px;font-weight:700;font-size:14px;line-height:21px;color:var(--ink)}

/* footer */
.footer{position:absolute;left:0;top:3660px;width:1200px;height:284px;background:var(--navy)}
.flinks{position:absolute;top:3774px;left:0;width:1200px;display:flex;justify-content:center;gap:28px;color:var(--white);font-size:15px;font-weight:500}
.flinks .sep{opacity:.6}
.social{position:absolute;top:3886px;left:534px;display:flex;gap:12px}
.social span{width:28px;height:28px;border-radius:50%;background:var(--white)}
.social span.on{background:var(--green)}
</style>
</head>
<body>

<!-- HERO -->
<header class="hero">
  <div class="shade" role="img" aria-label="Dark-toned photo of business people silhouetted in a bright office"></div>
  <div class="brand" style="left:36px;top:14px;font-size:28px">REACH CRAFTERS</div>
  <nav class="nav">
    <span class="active">Home</span><span>About Us</span><span>Services</span><span>Insights</span><span>Contact Us</span>
  </nav>
  <div class="btn" style="left:920px;top:12px;width:140px">Get Started</div>
  <h1>BE FOUND. BE CHOSEN.</h1>
  <div class="lead">Small and medium-sized business marketing consultancy</div>
  <div class="btn" style="left:402px;top:344px;width:230px;height:46px">Book a Strategy Call</div>
  <div class="btn ghost" style="left:652px;top:344px;width:146px;height:46px">Learn More</div>
</header>

<!-- ABOUT -->
<section class="about">
  <div class="abs" style="left:128px;top:672px;width:290px;height:334px;border:4px solid var(--purple)"></div>
  <div class="photo" style="left:144px;top:688px;width:312px;height:360px;background:linear-gradient(160deg,#ece8e0,#cbc3b6 50%,#7f7a73)" role="img" aria-label="Business team shaking hands in a bright office"></div>
  <div class="abs" style="left:656px;top:720px;font-family:var(--head);font-weight:600;font-size:38px;line-height:48px;letter-spacing:1px">ABOUT REACH CRAFTERS</div>
  <div class="rule" style="left:656px;top:788px"></div>
  <div class="abs about-text" style="left:656px;top:828px;width:400px"><p>Our work turns scattered marketing into a system that finds, qualifies and converts high-ticket clients. We bring business school frameworks and decision-grade intelligence to owners who want growth they can measure and repeat.</p></div>
  <div class="btn" style="left:656px;top:962px;width:140px">Read More</div>
</section>

<!-- SERVICES -->
<section class="services">
  <div class="title" style="top:1114px">OUR SERVICES</div>
  <div class="rule" style="left:570px;top:1182px"></div>
  <div class="svc" style="left:144px;width:296px;background:linear-gradient(150deg,#0d1a3a,#1e3f7a 50%,#0a1428)" role="img" aria-label="Hand touching a glowing digital data display">Demand Intelligence</div>
  <div class="svc" style="left:452px;width:296px;background:linear-gradient(150deg,#2cc489,#16a46c 60%,#0f8a5a)" role="img" aria-label="Team meeting around a table with green overlay">Go-To-Market Strategy</div>
  <div class="svc" style="left:760px;width:296px;background:linear-gradient(150deg,#4a4f5c,#2a2f3a 60%,#1c2029)" role="img" aria-label="Advisors discussing plans in a meeting room">Advisory &amp; Enablement</div>
  <div class="btn" style="left:528px;top:1542px;width:144px">Learn More</div>
</section>

<!-- PURPOSE / VIDEO -->
<section class="purpose">
  <div class="purpose-band"></div>
  <h2 class="title light" style="top:1716px">WHAT IT MEANS TO BE A REACH CRAFTER</h2>
  <div class="rule" style="left:570px;top:1780px"></div>
  <p class="purpose-text">Lorem ipsum dolor sit amet, consectetur adipiscing elit, sed do eiusmod tempor incididunt ut labore et dolore magna aliqua. Ut enim ad minim veniam, quis nostrud exercitation ullamco laboris nisi ut aliquip.</p>
  <div class="photo" style="left:204px;top:1900px;width:792px;height:388px;background:linear-gradient(120deg,#e4ebf2 0%,#c6d3e0 45%,#8d9cb0 100%)" role="img" aria-label="Explainer video still of a presenter at a screen showing charts"></div>
  <svg class="abs" style="left:572px;top:2066px" width="56" height="56" viewBox="0 0 56 56" aria-hidden="true">
    <circle cx="28" cy="28" r="28" fill="#7a5cf5"/>
    <path d="M22 17 L40 28 L22 39 Z" fill="#fff"/>
  </svg>
  <div class="btn" style="left:494px;top:2342px;width:212px">Book a Strategy Call</div>
</section>

<!-- GALLERY -->
<section class="gallery">
  <div class="title" style="top:2450px">OUR GALLERY</div>
  <div class="rule" style="left:570px;top:2518px"></div>
  <div class="photo" style="left:144px;top:2568px;width:296px;height:216px;background:linear-gradient(150deg,#8e9bb0,#3e4b63)" role="img" aria-label="Team reviewing a presentation board"></div>
  <div class="photo" style="left:452px;top:2568px;width:296px;height:216px;background:linear-gradient(150deg,#ddd3c6,#7c6a5a)" role="img" aria-label="Colleagues collaborating at a laptop"></div>
  <div class="photo" style="left:760px;top:2568px;width:296px;height:216px;background:linear-gradient(150deg,#eef0f3,#aab2bd)" role="img" aria-label="Professionals working at a bright desk"></div>
  <div class="photo" style="left:144px;top:2804px;width:296px;height:216px;background:linear-gradient(150deg,#5d6b82,#1f2a3e)" role="img" aria-label="Hands reviewing charts on a tablet"></div>
  <div class="photo" style="left:452px;top:2804px;width:296px;height:216px;background:linear-gradient(150deg,#dcd4c8,#6e6254)" role="img" aria-label="Business team meeting at a long table"></div>
  <div class="photo" style="left:760px;top:2804px;width:296px;height:216px;background:linear-gradient(150deg,#e4e8ec,#8d98a6)" role="img" aria-label="Presenter leading a strategy session"></div>
</section>

<!-- BLOG -->
<section>
  <div class="blog"></div>
  <div class="abs" style="left:144px;top:3152px;font-family:var(--head);font-weight:600;font-size:38px;line-height:48px;letter-spacing:1px">OUR BLOG</div>
  <div class="rule" style="left:144px;top:3218px"></div>
  <div class="btn" style="left:912px;top:3172px;width:144px">Learn More</div>
  <svg class="abs" style="left:98px;top:3406px" width="20" height="28" viewBox="0 0 20 28" aria-hidden="true"><path d="M15 3 L5 14 L15 25" stroke="#161c2c" stroke-width="3" fill="none"/></svg>
  <svg class="abs" style="left:1082px;top:3406px" width="20" height="28" viewBox="0 0 20 28" aria-hidden="true"><path d="M5 3 L15 14 L5 25" stroke="#161c2c" stroke-width="3" fill="none"/></svg>
  <article class="card" style="left:144px">
    <div class="img" style="background:linear-gradient(150deg,#9fb0c4,#3f5070)" role="img" aria-label="Team in a meeting celebrating results"></div>
    <div class="date"><svg width="14" height="14" viewBox="0 0 14 14" aria-hidden="true"><rect x="1" y="2" width="12" height="11" fill="none" stroke="#7a5cf5" stroke-width="1.5"/><line x1="1" y1="5.5" x2="13" y2="5.5" stroke="#7a5cf5" stroke-width="1.5"/></svg>November 5, 2020</div>
    <h3>Lorem ipsum dolorsance, consectetur adipiscing elit, sed do eiusmod</h3>
  </article>
  <article class="card" style="left:452px">
    <div class="img" style="background:linear-gradient(150deg,#e6ebf2,#9eacc0)" role="img" aria-label="Presenter pointing at a chart on a screen"></div>
    <div class="date"><svg width="14" height="14" viewBox="0 0 14 14" aria-hidden="true"><rect x="1" y="2" width="12" height="11" fill="none" stroke="#7a5cf5" stroke-width="1.5"/><line x1="1" y1="5.5" x2="13" y2="5.5" stroke="#7a5cf5" stroke-width="1.5"/></svg>November 5, 2020</div>
    <h3>Lorem ipsum dolorsance, consectetur adipiscing elit, sed do eiusmod</h3>
  </article>
  <article class="card" style="left:760px">
    <div class="img" style="background:linear-gradient(150deg,#dfe6f0,#5f769c)" role="img" aria-label="Printed charts and graphs on a desk"></div>
    <div class="date"><svg width="14" height="14" viewBox="0 0 14 14" aria-hidden="true"><rect x="1" y="2" width="12" height="11" fill="none" stroke="#7a5cf5" stroke-width="1.5"/><line x1="1" y1="5.5" x2="13" y2="5.5" stroke="#7a5cf5" stroke-width="1.5"/></svg>November 5, 2020</div>
    <h3>Lorem ipsum dolorsance, consectetur adipiscing elit, sed do eiusmod</h3>
  </article>
</section>

<!-- FOOTER -->
<footer>
  <div class="footer"></div>
  <div class="brand" style="left:0;width:1200px;text-align:center;top:3710px;font-size:30px">REACH CRAFTERS</div>
  <div class="flinks"><span>HOME</span><span class="sep">|</span><span>ABOUT US</span><span class="sep">|</span><span>SERVICES</span><span class="sep">|</span><span>INSIGHTS</span><span class="sep">|</span><span>CONTACT US</span></div>
  <div class="abs" style="left:144px;top:3822px;width:912px;height:1px;background:rgba(255,255,255,.2)"></div>
  <div class="abs" style="left:0;top:3842px;width:1200px;text-align:center;color:var(--white);font-size:14px">© 2026 Reach Crafters - All Rights Reserved</div>
  <div class="social"><span></span><span></span><span class="on"></span><span></span></div>
</footer>

</body>
</html>
```